Web Developer Needs a Business Card Design

I need a personal business card design that represents me as a web developer for potential employers. I would like the background to be a dark color on the front for contrast with my logo and name. The back will have all my information along with a smaller version of the logo. I want something with a modern look and feel, not too conservative. This will be used for potential employers and freelance work.

Industry/Entity Type

Business

Contact Information for Business Card

Front should have my logo and name. The back should have all my personal information which would include: name: Tom Varulek, phone: 570-614-3098, email: tomvarulek@quillbox.net, website url: www.tomvarulek.net, logo, web developer.

Font styles to use
Sans Serif

Requirements
Must have
• Must include my logo. The color palette base color will be the logo color.

```html
<!DOCTYPE html>
<html lang="en">
<head>
<meta charset="utf-8">
<title>Tom Varulek – Business Card</title>
<link href="https://fonts.googleapis.com/css2?family=Roboto:wght@400;500&display=swap" rel="stylesheet">
<style>
  :root {
    --teal: #4fe0bd;
    --teal-soft: #7debd0;
    --ink: #0d0d0e;
    --ink-2: #1c1d1f;
    --paper: #ffffff;
    --text: #1a1a1a;
    --stage: #e4e4e4;
  }
  * { margin: 0; padding: 0; box-sizing: border-box; }
  html, body { width: 1200px; height: 1200px; overflow: hidden; }
  body {
    background: var(--stage);
    font-family: "Roboto", Arial, sans-serif;
    display: flex;
    flex-direction: column;
    align-items: center;
    justify-content: center;
    gap: 60px;
  }
  .card {
    position: relative;
    width: 840px;
    height: 480px;
    border-radius: 26px;
    overflow: hidden;
  }
  .card-front {
    background: linear-gradient(135deg, var(--ink-2) 0%, var(--ink) 55%, #050505 100%);
    display: flex;
    align-items: center;
    justify-content: center;
  }
  .brand {
    display: flex;
    align-items: center;
    gap: 18px;
    color: var(--teal);
    font-weight: 500;
  }
  .brand-dot {
    border-radius: 50%;
    background: var(--teal);
    flex: none;
  }
  .card-front .brand { font-size: 52px; }
  .card-front .brand-dot { width: 40px; height: 40px; }

  .card-back { background: var(--paper); }
  .back-waves { position: absolute; inset: 0; width: 100%; height: 100%; }
  .identity {
    position: absolute;
    top: 38px;
    right: 56px;
    text-align: right;
    color: var(--teal);
  }
  .identity-name { font-size: 34px; font-weight: 400; letter-spacing: 0.5px; }
  .identity-role { font-size: 17px; margin-top: 2px; }
  .card-back .brand {
    position: absolute;
    left: 70px;
    top: 300px;
    font-size: 38px;
  }
  .card-back .brand-dot { width: 30px; height: 30px; }
  .contacts {
    position: absolute;
    left: 500px;
    top: 250px;
    list-style: none;
    color: var(--text);
    font-size: 21px;
  }
  .contacts li {
    display: flex;
    align-items: center;
    gap: 16px;
    height: 34px;
  }
  .contacts svg { width: 18px; height: 18px; fill: var(--teal); flex: none; }
</style>
</head>
<body>

<section class="card card-front">
  <div class="brand"><span class="brand-dot"></span>Tom Varulek</div>
</section>

<section class="card card-back">
  <svg class="back-waves" viewBox="0 0 840 480" preserveAspectRatio="none" aria-hidden="true">
    <path d="M0 0 H840 V110 C700 150 560 120 430 150 C250 190 90 230 0 330 Z" fill="var(--ink)"/>
    <path d="M0 330 C90 230 250 190 430 150 C560 125 700 150 840 110 L840 118 C700 160 560 138 440 162 C270 198 120 240 20 340 Z" fill="var(--teal)"/>
    <path d="M40 320 C150 230 300 200 450 172 C590 148 720 160 840 130 L840 134 C720 168 590 158 455 182 C310 210 170 245 40 320 Z" fill="var(--teal-soft)"/>
  </svg>

  <div class="identity">
    <div class="identity-name">Tom Varulek</div>
    <div class="identity-role">Web Developer</div>
  </div>

  <div class="brand"><span class="brand-dot"></span>Tom Varulek</div>

  <ul class="contacts">
    <li>
      <svg viewBox="0 0 24 24" aria-hidden="true"><path d="M6.6 10.8a15 15 0 0 0 6.6 6.6l2.2-2.2c.3-.3.7-.4 1-.2 1.1.4 2.3.6 3.6.6.6 0 1 .4 1 1V20c0 .6-.4 1-1 1A17 17 0 0 1 3 4c0-.6.4-1 1-1h3.5c.6 0 1 .4 1 1 0 1.3.2 2.5.6 3.6.1.3 0 .7-.2 1z"/></svg>
      570-614-3098
    </li>
    <li>
      <svg viewBox="0 0 24 24" aria-hidden="true"><path d="M2 5h20v14H2z M3 6l9 7 9-7" stroke="#fff" stroke-width="1.5"/></svg>
      tomvarulek@quillbox.net
    </li>
    <li>
      <svg viewBox="0 0 24 24" aria-hidden="true"><circle cx="12" cy="12" r="10"/><path d="M2 12h20M12 2c3 3 3 17 0 20M12 2c-3 3-3 17 0 20" stroke="#fff" stroke-width="1.3" fill="none"/></svg>
      www.tomvarulek.net
    </li>
  </ul>
</section>

</body>
</html>
```